Develop website for Cloud Security Startup

Looking for a logo that conveys the outsourced security and management of clients data, systems and development in Tellix, Bri and Pindle with an emphasis on security and compliance

Target Market(s)

Companies looking for professional services IT firm

Coding

Coded - Design and coding required

Number of Pages Required

5+ page

Font styles to use
Sans Serif

Colors
0455a3
33a6d7

Requirements
Must have
• Landing Page
- Help me get started

Move to the cloud safely
- Benefits of Cloud

What we do
- Cloud Adoption
- Managed Services
- Optimise

Resources
- News
- Resources
- Events
- Webinars
- Not for profit
- Case Studies
- Support Button
- Incident Button

Company
- About Us
- Why Vorplexa?
- Acreditations
- Quorvane Tellix Partner
- Net Promoter Score
- Careers
- Contact Us

Contact Us

```html
<!DOCTYPE html>
<html lang="en">
<head>
<meta charset="utf-8">
<title>Vorplexa Effective Technology Management</title>
<link href="https://fonts.googleapis.com/css2?family=Cinzel:wght@600;700&family=Lato:wght@400;700&display=swap" rel="stylesheet">
<style>
:root{
  --primary:#0455a3;
  --heading:#0d4a9a;
  --accent:#33a6d7;
  --text:#3a3a3a;
  --muted:#666;
  --grey-bg:#f3f3f3;
  --footer:#0f46a0;
  --white:#fff;
}
*{box-sizing:border-box;margin:0;padding:0}
html,body{width:1200px;height:3760px;overflow:hidden}
body{font-family:'Lato',sans-serif;color:var(--text);background:var(--white)}
a{color:inherit;text-decoration:none}
.serif-title{font-family:'Cinzel',serif;font-weight:700;color:var(--heading);letter-spacing:1px}

/* header */
.site-header{height:115px;display:flex;align-items:center;justify-content:space-between;padding:0 110px}
.brand{display:flex;align-items:center;gap:10px}
.brand-dot{width:34px;height:34px;background:var(--primary);border-radius:50%}
.brand-name{font-size:26px;font-weight:700;color:var(--primary);letter-spacing:1px;line-height:1}
.brand-tag{font-size:7px;color:var(--primary);letter-spacing:.5px;margin-top:3px}
.main-nav{display:flex;gap:36px;font-size:14px;color:var(--accent);font-weight:400}
.main-nav a.active{color:var(--primary);font-weight:700;border-bottom:3px solid var(--primary);padding-bottom:6px}

/* hero */
.hero{height:571px;position:relative;background:radial-gradient(ellipse at 50% 35%,#48566a 0%,#1e2530 45%,#0c0f14 100%);text-align:center;color:var(--white)}
.hero-title{position:absolute;top:322px;left:0;right:0;font-family:'Cinzel',serif;font-weight:600;font-size:34px;letter-spacing:1px}
.hero-text{position:absolute;top:370px;left:120px;right:120px;font-size:18px;line-height:25px}
.btn-solid{display:inline-block;background:var(--primary);color:var(--white);font-weight:700;font-size:17px;padding:12px 20px}
.hero .btn-solid{position:absolute;top:440px;left:523px}
.hero-dots{position:absolute;top:630px;left:0;right:0;display:flex;justify-content:center;gap:4px}
.hero-dots span{width:13px;height:13px;border:2px solid #fff;border-radius:50%}
.hero-dots span.on{background:#fff}

/* benefits */
.benefits{height:514px;position:relative}
.photo-frame{position:absolute;border:1px solid #ddd;padding:8px;background:#fff;box-shadow:0 0 4px rgba(0,0,0,.08)}
.benefits .photo-frame{left:110px;top:70px;width:485px;height:361px}
.photo{width:100%;height:100%}
.benefits-copy{position:absolute;left:654px;top:82px;width:436px}
.benefits-copy h2{font-size:36px;margin-bottom:10px}
.benefits-copy p{font-size:14.5px;line-height:26.5px;color:var(--text);margin-bottom:13px}

/* services */
.services{height:680px;background:var(--grey-bg);position:relative}
.section-title{text-align:center;font-size:36px;position:absolute;left:0;right:0}
.services .section-title{top:52px}
.slider-arrow{position:absolute;width:30px;height:50px}
.cards{position:absolute;top:146px;left:110px;display:flex;gap:27px}
.card{width:308px;height:450px;background:#fff;box-shadow:0 1px 4px rgba(0,0,0,.12)}
.card-img{height:212px}
.card-body{padding:24px 25px}
.card h3{color:var(--primary);font-size:20px;font-weight:700;margin-bottom:10px}
.card p{font-size:12px;line-height:21.5px;color:var(--muted)}
.btn-outline{display:inline-block;border:1.5px solid var(--primary);color:var(--primary);font-weight:700;font-size:14px;padding:10px 20px;margin-top:22px;border-radius:2px}

/* resources */
.resources{height:438px;background:linear-gradient(180deg,#47a6dc 0%,#2f86c8 70%,#3b9bd6 100%);color:#fff;text-align:center;position:relative}
.resources .section-title{top:60px;color:#fff}
.resources-copy{position:absolute;top:126px;left:138px;right:138px;font-size:14.5px;line-height:25px}
.resources-copy p{margin-bottom:12px}
.btn-white{position:absolute;top:314px;left:524px;background:#fff;color:var(--primary);font-weight:700;font-size:17px;padding:11px 19px}

/* company */
.company{height:756px;background:var(--grey-bg);position:relative}
.company .section-title{top:58px}
.company .photo-frame{left:234px;top:132px;width:751px;height:437px}
.play{position:absolute;left:333px;top:180px;width:80px;height:80px}
.company-text{position:absolute;top:600px;left:240px;right:240px;text-align:center;font-size:14px;line-height:25px}

/* partners */
.partners{height:291px;position:relative}
.partners .section-title{top:68px}
.logo-row{position:absolute;top:154px;left:112px;display:flex;gap:13px}
.logo-tile{width:152px;height:75px;background:#fff;box-shadow:0 1px 4px rgba(0,0,0,.15);display:flex;align-items:center;justify-content:center;font-size:15px;font-weight:700;color:#333;text-align:center;line-height:1.1}

/* footer */
.site-footer{height:395px;background:var(--footer);color:#fff;position:relative}
.foot-col{position:absolute;top:45px}
.foot-col h4{font-size:17px;font-weight:700;letter-spacing:.5px;margin:0 0 10px 2px}
.foot-col ul{list-style:none;font-size:12.5px}
.foot-col li{height:32px;line-height:32px}
.newsletter-note{font-size:11px;margin:4px 0 12px}
.email-box{width:240px;height:45px;background:#fff;color:#444;font-size:12.5px;display:flex;align-items:center;justify-content:space-between;padding:0 16px}
.social-title{margin-top:24px!important}
.socials{display:flex;gap:13px;margin-top:14px}
.socials span{width:36px;height:36px;border:1.5px solid #fff;border-radius:50%}
.copyright{position:absolute;bottom:0;left:0;right:0;height:46px;border-top:1px solid rgba(255,255,255,.2);text-align:center;line-height:46px;font-size:11px}
</style>
</head>
<body>

<header class="site-header">
  <div class="brand">
    <span class="brand-dot"></span>
    <div>
      <div class="brand-name">VORPLEXA</div>
      <div class="brand-tag">EFFECTIVE TECHNOLOGY MANAGEMENT</div>
    </div>
  </div>
  <nav class="main-nav">
    <a class="active" href="#">HOME</a>
    <a href="#">BENEFITS OF CLOUD</a>
    <a href="#">WHAT WE DO</a>
    <a href="#">RESOURCES</a>
    <a href="#">COMPANY</a>
    <a href="#">CONTACT US</a>
  </nav>
</header>

<section class="hero" role="img" aria-label="Dark photo of a hand holding a cloud with a padlock">
  <h1 class="hero-title">VORPLEXA EFFECTIVE TECHNOLOGY MANAGEMENT</h1>
  <p class="hero-text">We are a cloud security startup outsourcing security and management of clients data, systems and development in Tellix, Bri and Pindle with an emphasis on security and compliance.</p>
  <a class="btn-solid" href="#">LEARN MORE</a>
  <div class="hero-dots"><span class="on"></span><span></span><span></span><span></span></div>
</section>

<section class="benefits">
  <div class="photo-frame">
    <div class="photo" role="img" aria-label="Cloud computing devices above a tablet" style="background:linear-gradient(160deg,#9cb6cf 0%,#3c6fb0 45%,#1d3f73 100%)"></div>
  </div>
  <div class="benefits-copy">
    <h2 class="serif-title">BENEFITS OF CLOUD</h2>
    <p>Lorem ipsum dolor sit amet, consectetur adipiscing elit, sed do eiusmod tempor incididunt ut labore et dolore magna aliqua. Ut enim ad minim veniam, quis nostrud exercitation ullamco laboris nisi ut aliquip ex ea commodo consequat. Duis aute irure dolor in reprehenderit in voluptate velit esse cillum dolore eu fugiat nulla pariatur. Excepteur sint occaecat cupidatat non proident, sunt in culpa qui officia deserunt mollit anim id est laborum</p>
    <p>Quis autem vel eum iure reprehenderit qui in ea voluptate velit esse quam nihil molestiae consequatur.</p>
  </div>
</section>

<section class="services">
  <h2 class="section-title serif-title">WHAT WE DO</h2>
  <svg class="slider-arrow" style="left:46px;top:1515px;top:315px" viewBox="0 0 30 50"><path d="M24 3 4 25l20 22" fill="none" stroke="#888" stroke-width="2.5"/></svg>
  <svg class="slider-arrow" style="left:1116px;top:315px" viewBox="0 0 30 50"><path d="M6 3l20 22L6 47" fill="none" stroke="#888" stroke-width="2.5"/></svg>
  <div class="cards">
    <article class="card">
      <div class="card-img" role="img" aria-label="Person facing a circuit cloud wall" style="background:linear-gradient(180deg,#3a5f99,#0f2346)"></div>
      <div class="card-body">
        <h3>CLOUD ADOPTION</h3>
        <p>Nam libero tempore, cum soluta nobis est eligendi optio cumque nihil impedit quo minus id quod maxime placeat facere possimus, omnis voluptas assumenda est.</p>
        <a class="btn-outline" href="#">LEARN MORE</a>
      </div>
    </article>
    <article class="card">
      <div class="card-img" role="img" aria-label="Office desk with laptop and plant" style="background:linear-gradient(180deg,#8ca0bd,#2f4f86)"></div>
      <div class="card-body">
        <h3>MANAGED SERVICES</h3>
        <p>Nam libero tempore, cum soluta nobis est eligendi optio cumque nihil impedit quo minus id quod maxime placeat facere possimus, omnis voluptas assumenda est.</p>
        <a class="btn-outline" href="#">LEARN MORE</a>
      </div>
    </article>
    <article class="card">
      <div class="card-img" role="img" aria-label="Team joining puzzle pieces" style="background:linear-gradient(180deg,#4d6491,#1c3566)"></div>
      <div class="card-body">
        <h3>OPTIMISE</h3>
        <p>Nam libero tempore, cum soluta nobis est eligendi optio cumque nihil impedit quo minus id quod maxime placeat facere possimus, omnis voluptas assumenda est.</p>
        <a class="btn-outline" href="#">LEARN MORE</a>
      </div>
    </article>
  </div>
</section>

<section class="resources" role="img" aria-label="Blue city network backdrop">
  <h2 class="section-title serif-title">OUR RESOURCES</h2>
  <div class="resources-copy">
    <p>Sed ut perspiciatis unde omnis iste natus error sit voluptatem accusantium doloremque laudantium, totam rem aperiam, eaque ipsa quae ab illo inventore veritatis et quasi architecto beatae vitae dicta sunt explicabo. Nemo enim ipsam voluptatem quia voluptas sit aspernatur aut odit aut fugit, sed quia consequuntur magni dolores eos qui ratione voluptatem sequi nesciunt. Neque porro quisquam est, qui dolorem ipsum quia dolor sit amet, consectetur, adipisci velit, sed quia non numquam eius modi tempora incidunt ut labore</p>
    <p>At vero eos et accusamus et iusto odio dignissimos ducimus qui blanditiis praesentium voluptatum deleniti atque corrupti quos dolores et quas molestias excepturi sint occaecati cupiditate non provident.</p>
  </div>
  <a class="btn-white" href="#">LEARN MORE</a>
</section>

<section class="company">
  <h2 class="section-title serif-title">OUR COMPANY</h2>
  <div class="photo-frame">
    <div class="photo" role="img" aria-label="Hands typing on a laptop with glowing network lines" style="background:linear-gradient(135deg,#1d2a4a 0%,#4e6db8 50%,#c7d3f3 100%);position:relative">
      <svg class="play" viewBox="0 0 80 80"><circle cx="40" cy="40" r="40" fill="#0d3f94"/><path d="M31 24v32l26-16z" fill="#fff"/></svg>
    </div>
  </div>
  <p class="company-text">But I must explain to you how all this mistaken idea of denouncing pleasure and praising pain was born and I will give you a complete account of the system, and expound the actual teachings of the great explorer of the truth, the master-builder of human happiness.</p>
</section>

<section class="partners">
  <h2 class="section-title serif-title">CLIENT PARTNERS</h2>
  <svg class="slider-arrow" style="left:55px;top:165px" viewBox="0 0 30 50"><path d="M22 10 8 25l14 15" fill="none" stroke="#999" stroke-width="3"/></svg>
  <svg class="slider-arrow" style="left:1115px;top:165px" viewBox="0 0 30 50"><path d="M8 10l14 15L8 40" fill="none" stroke="#999" stroke-width="3"/></svg>
  <div class="logo-row">
    <div class="logo-tile">Tramlo</div>
    <div class="logo-tile">Hallowmere<br>College</div>
    <div class="logo-tile">Penrith Vale</div>
    <div class="logo-tile">Oskar Institute</div>
    <div class="logo-tile">Kestrel School</div>
    <div class="logo-tile">Coleg Farrow</div>
  </div>
</section>

<footer class="site-footer">
  <div class="foot-col" style="left:110px">
    <h4>Company</h4>
    <ul><li>About Us</li><li>Why Vorplexa?</li><li>Acreditations</li><li>Quorvane Tellix Partner</li><li>Net Promoter Score</li><li>Careers</li><li>Contact Us</li></ul>
  </div>
  <div class="foot-col" style="left:357px">
    <h4>Resources</h4>
    <ul><li>News</li><li>Resources</li><li>Events</li><li>Webinars</li><li>Not for profit</li><li>Case Studies</li><li>Support Button</li></ul>
  </div>
  <div class="foot-col" style="left:580px">
    <h4>What We Do</h4>
    <ul><li>Cloud Adoption</li><li>Managed Services</li><li>Optimise</li><li>Other Services</li></ul>
  </div>
  <div class="foot-col" style="left:850px">
    <h4>Newsletter</h4>
    <p class="newsletter-note">Lorem Ipsum is simply dummy</p>
    <div class="email-box"><span>Type Your Email Here</span>
      <svg width="40" height="10" viewBox="0 0 40 10"><path d="M0 5h38M33 1l5 4-5 4" fill="none" stroke="#7aa0d0" stroke-width="1.2"/></svg>
    </div>
    <h4 class="social-title">Social Media</h4>
    <div class="socials" aria-label="Social media links"><span></span><span></span><span></span><span></span></div>
  </div>
  <div class="copyright">Copyrights © 2021 VORPLEXA EFFECTIVE TECHNOLOGY MANAGEMENT. All rights reserved</div>
</footer>

</body>
</html>
```